Verodex business card

Business card for sustainable investment company called "Verodex". Verodex is an exchange platform selling carbon credits between buyers and sellers. Carbon Credits are an environmental commodity for reducing global carbon emissions.

the card should obviously have our logo and the theme should be sustainability/environment mixed with a trading platform.

Contact Information for Business Card

Logo, Name, Title, Phone, Email

Colors
0054AA
0677BA
7BADD7
CADEEF
E8F1F8
0094D4
00A9DD
6FCCEA
C7EBF8
E9F6FB
00AB8E
00BBA5
67D7C9
C6EFE9
E9F9F6
59FF00
82FF00
B8FF75
E3FFCB
F4FFEA

```html
<!DOCTYPE html>
<html lang="en">
<head>
<meta charset="utf-8">
<title>Verodex Business Card</title>
<link href="https://fonts.googleapis.com/css2?family=Open+Sans:wght@400;600;700;800&display=swap" rel="stylesheet">
<style>
  :root {
    --backdrop: #4b4b4b;
    --navy: #152b52;
    --ink: #111111;
    --white: #ffffff;
    --teal: #64c9d9;
    --blue: #4a7cc8;
    --mid: #4fa3d6;
  }
  * { margin: 0; padding: 0; box-sizing: border-box; }
  html, body {
    width: 1200px; height: 780px; overflow: hidden;
    background: var(--backdrop);
    font-family: "Open Sans", Arial, sans-serif;
  }
  .stage {
    position: relative; width: 1200px; height: 780px;
    display: flex; align-items: center; justify-content: center; gap: 40px;
  }
  .card {
    position: relative; width: 560px; height: 320px; overflow: hidden;
    box-shadow: 0 6px 18px rgba(0,0,0,.35);
  }
  .card-back { background: var(--navy); display: flex; align-items: center; justify-content: center; }
  .card-front { background: var(--white); }

  .brand { display: flex; align-items: center; gap: 16px; }
  .brand-mark { width: 50px; height: 50px; background: linear-gradient(135deg, var(--teal), var(--blue)); }
  .brand-name { font-weight: 800; font-size: 46px; letter-spacing: 1px; color: var(--white); line-height: 1; }
  .card-front .brand { position: absolute; left: 34px; top: 132px; gap: 12px; }
  .card-front .brand-mark { width: 40px; height: 40px; }
  .card-front .brand-name { font-size: 33px; color: var(--navy); }

  .divider { position: absolute; left: 298px; top: 52px; width: 1.5px; height: 176px; background: var(--navy); }

  .details { position: absolute; left: 322px; top: 62px; }
  .person-name {
    font-weight: 800; font-size: 25px; line-height: 1.1;
    background: linear-gradient(90deg, var(--teal), var(--blue));
    -webkit-background-clip: text; background-clip: text; color: transparent;
  }
  .person-title { font-weight: 600; font-size: 14px; color: var(--ink); margin-top: 2px; }
  .contacts { list-style: none; margin-top: 24px; }
  .contacts li { display: flex; align-items: center; gap: 9px; font-size: 14px; color: var(--ink); line-height: 1.5; }
  .contacts svg { width: 14px; height: 14px; flex: none; }

  .address-band {
    position: absolute; left: 0; top: 262px; width: 478px; height: 28px;
    background: linear-gradient(90deg, var(--teal), var(--mid) 60%, var(--blue));
    color: var(--white); font-size: 15px; font-weight: 400;
    display: flex; align-items: center; justify-content: flex-end; padding-right: 18px;
  }
  .corner-block {
    position: absolute; left: 478px; top: 252px; width: 82px; height: 38px;
    background: var(--navy); display: flex; align-items: center; justify-content: center;
  }
  .corner-dot { width: 24px; height: 24px; border-radius: 50%; background: linear-gradient(135deg, var(--teal), var(--blue)); }
</style>
</head>
<body>
<main class="stage">
  <section class="card card-back" aria-label="Card back">
    <div class="brand">
      <span class="brand-mark"></span>
      <span class="brand-name">VERODEX</span>
    </div>
  </section>

  <section class="card card-front" aria-label="Card front">
    <div class="brand">
      <span class="brand-mark"></span>
      <span class="brand-name">VERODEX</span>
    </div>
    <div class="divider"></div>
    <div class="details">
      <p class="person-name">Lena Marovic</p>
      <p class="person-title">Managing Director</p>
      <ul class="contacts">
        <li>
          <svg viewBox="0 0 24 24" aria-hidden="true"><path fill="#4fa3d6" d="M6.6 10.8a15.1 15.1 0 0 0 6.6 6.6l2.2-2.2c.3-.3.7-.4 1-.2 1.1.4 2.3.6 3.6.6.6 0 1 .4 1 1V20c0 .6-.4 1-1 1A17 17 0 0 1 3 4c0-.6.4-1 1-1h3.5c.6 0 1 .4 1 1 0 1.3.2 2.5.6 3.6.1.3 0 .7-.2 1z"/></svg>
          (555) 014-2298
        </li>
        <li>
          <svg viewBox="0 0 24 24" aria-hidden="true"><rect x="2" y="5" width="20" height="14" rx="1.5" fill="#4fa3d6"/><path d="M3 6l9 7 9-7" fill="none" stroke="#fff" stroke-width="1.6"/></svg>
          info@verodex.com
        </li>
        <li>
          <svg viewBox="0 0 24 24" aria-hidden="true"><circle cx="12" cy="12" r="10" fill="#4fa3d6"/><path d="M2 12h20M12 2c3 3 3 17 0 20M12 2c-3 3-3 17 0 20" fill="none" stroke="#fff" stroke-width="1.2"/></svg>
          www.verodex.com
        </li>
      </ul>
    </div>
    <div class="address-band">480 Elmgrove Ave. Suite 120 Denton, TX 76201</div>
    <div class="corner-block"><span class="corner-dot"></span></div>
  </section>
</main>
</body>
</html>
```